Business card design for Automotive workshop

We need a business card for a new automotive repair and tyre shop called Keelstone Prime Automotive located in New Zealand. We are a clean, modern and fresh workshop and company.

Front needs to feature logo,
my name:
Marlo Fenwicke (director)

Address:
48 Tarn Lane
Corrowick 3592

Phone: 07 594 2713
Mobile: 027 451 9362
Email: office@keelstoneautomotive.example.nz
Website: keelstoneautomotive.example.nz

Back needs to feature an area to write down appointment details, date and time.

Also feature a list of jobs and work we do such as,
Vehicle Servicing
All Mechanical Repairs
Warrant of Fitness
Tyres & Wheel Alignments
Automotive Diagnostics
Automotive Parts & Supplies

```html
<!DOCTYPE html>
<html lang="en">
<head>
<meta charset="utf-8">
<title>Keelstone Prime Automotive – Business Card</title>
<link href="https://fonts.googleapis.com/css2?family=Montserrat:wght@400;500;700&family=Roboto:wght@400;500;700&display=swap" rel="stylesheet">
<style>
  :root {
    --page: #1b1b1c;
    --card-dark: #1a1a1b;
    --card-dark-2: #2a2b2d;
    --paper: #ffffff;
    --red: #e0202a;
    --white: #f4f4f4;
    --ink: #1c1c1c;
    --rule: #6a6a6a;
  }
  * { box-sizing: border-box; margin: 0; padding: 0; }
  html, body { width: 1200px; height: 900px; overflow: hidden; }
  body {
    background: var(--page);
    font-family: "Roboto", Arial, sans-serif;
    position: relative;
  }
  .card {
    position: absolute;
    left: 330px;
    width: 540px;
    height: 309px;
    border-radius: 18px;
    overflow: hidden;
    box-shadow: 0 14px 34px rgba(0,0,0,.55);
  }

  /* ---------- Back ---------- */
  .card--back { top: 60px; background: var(--paper); }
  .back__band {
    height: 96px;
    background: linear-gradient(180deg, var(--card-dark-2), var(--card-dark));
    display: flex; align-items: center; justify-content: center;
  }
  .wordmark {
    display: flex; align-items: center; gap: 12px;
    font-family: "Montserrat", Arial, sans-serif;
    font-weight: 700;
    color: var(--white);
    letter-spacing: 2px;
    text-transform: uppercase;
    white-space: nowrap;
  }
  .wordmark__square { width: 14px; height: 14px; background: var(--red); }
  .back__band .wordmark { font-size: 22px; }
  .appointment { padding: 20px 38px 0; font-size: 11px; color: var(--ink); }
  .appointment__row { display: flex; align-items: flex-end; gap: 8px; height: 34px; }
  .appointment__label { white-space: nowrap; padding-bottom: 3px; }
  .appointment__line { flex: 1; border-bottom: 1px solid var(--rule); height: 1px; }
  .services {
    position: absolute; left: 0; right: 0; bottom: 26px;
    text-align: center; font-size: 11.5px; color: var(--ink); line-height: 1.6;
    white-space: nowrap;
  }
  .services span.sep { margin: 0 7px; }

  /* ---------- Front ---------- */
  .card--front {
    top: 430px;
    background: radial-gradient(ellipse at 55% 35%, #35373a 0%, var(--card-dark) 70%);
  }
  .front__decor {
    position: absolute; right: 0; top: 0; width: 170px; height: 180px;
    background: radial-gradient(circle at 70% 40%, rgba(255,255,255,.05), rgba(255,255,255,0) 70%);
  }
  .front__logo { position: absolute; left: 0; right: 0; top: 70px; display: flex; justify-content: center; }
  .front__logo .wordmark { font-size: 24px; }
  .front__details {
    position: absolute; left: 40px; right: 20px; top: 150px;
    display: flex; align-items: stretch;
  }
  .person { flex: 0 0 215px; text-align: right; padding-right: 20px; }
  .person__name { font-family: "Roboto", Arial, sans-serif; font-weight: 700; color: var(--red); font-size: 24px; white-space: nowrap; }
  .person__role { font-family: "Montserrat", Arial, sans-serif; color: var(--white); font-size: 12px; margin-top: 3px; }
  .person__address { font-family: "Montserrat", Arial, sans-serif; color: var(--white); font-size: 11.5px; margin-top: 12px; line-height: 1.35; }
  .divider { width: 1px; background: var(--red); }
  .contacts { list-style: none; padding-left: 20px; font-family: "Montserrat", Arial, sans-serif; color: var(--white); font-size: 11px; }
  .contacts li { display: flex; align-items: center; gap: 10px; height: 23px; white-space: nowrap; }
  .contacts svg { width: 14px; height: 14px; flex: none; }
</style>
</head>
<body>

<section class="card card--back" aria-label="Card back">
  <div class="back__band">
    <div class="wordmark"><span class="wordmark__square"></span>Keelstone Prime Automotive</div>
  </div>
  <div class="appointment">
    <div class="appointment__row"><span class="appointment__label">Appointment details:</span><span class="appointment__line"></span></div>
    <div class="appointment__row"><span class="appointment__line"></span></div>
    <div class="appointment__row">
      <span class="appointment__label">Date:</span><span class="appointment__line"></span>
      <span class="appointment__label">Time:</span><span class="appointment__line"></span>
    </div>
  </div>
  <div class="services">
    <div>Vehicle Servicing<span class="sep">|</span>All Mechanical Repairs<span class="sep">|</span>Warrant of Fitness<span class="sep">|</span>Tyres &amp; Wheel Alignments</div>
    <div>Automotive Diagnostics<span class="sep">|</span>Automotive Parts &amp; Supplies</div>
  </div>
</section>

<section class="card card--front" aria-label="Card front">
  <div class="front__decor" role="img" aria-label="Faint workshop gear decoration"></div>
  <div class="front__logo">
    <div class="wordmark"><span class="wordmark__square"></span>Keelstone Prime Automotive</div>
  </div>
  <div class="front__details">
    <div class="person">
      <div class="person__name">Marlo Fenwicke</div>
      <div class="person__role">Director</div>
      <div class="person__address">48 Tarn Lane<br>Corrowick 3592</div>
    </div>
    <div class="divider"></div>
    <ul class="contacts">
      <li>
        <svg viewBox="0 0 16 16" fill="none" stroke="#e0202a" stroke-width="1.4"><path d="M2 5c0-2 2-3 6-3s6 1 6 3l-2 1-1-2H5L4 6 2 5z"/><rect x="3.5" y="7" width="9" height="7" rx="1"/><circle cx="8" cy="10.5" r="1.6"/></svg>
        07 594 2713
      </li>
      <li>
        <svg viewBox="0 0 16 16" fill="none" stroke="#e0202a" stroke-width="1.4"><rect x="4.5" y="1.5" width="7" height="13" rx="1.2"/><line x1="7" y1="12.2" x2="9" y2="12.2"/></svg>
        027 451 9362
      </li>
      <li>
        <svg viewBox="0 0 16 16" fill="none" stroke="#e0202a" stroke-width="1.4"><rect x="1.5" y="3.5" width="13" height="9"/><path d="M1.5 3.5L8 9l6.5-5.5"/></svg>
        office@keelstoneautomotive.example.nz
      </li>
      <li>
        <svg viewBox="0 0 16 16" fill="none" stroke="#e0202a" stroke-width="1.3"><circle cx="8" cy="8" r="6.5"/><ellipse cx="8" cy="8" rx="2.8" ry="6.5"/><line x1="1.5" y1="8" x2="14.5" y2="8"/></svg>
        keelstoneautomotive.example.nz
      </li>
    </ul>
  </div>
</section>

</body>
</html>
```